Corvane Lending Partners. Professional and Established Company

A full service finance company specializing in obtaining capital for small business. Business Lending advisor, helping small business owners access the capital they need to launch, grow, or sustain their business. Many of our programs offer flexible guidelines to overcome common obstacles such as credit score, credit history, and time in business, financials, and industry type. Our streamlined funding process makes getting a business loan, business line of credit, stated income commercial real estate loan, a smooth and stress free experience.SOME OF THE MOST COMMON NEEDS FOR BUSINESS CAPITAL:• Working Capital• Debt Consolidations (loans, merchant cash advances, etc.)• Payroll• Operating Expenses• Inventory• Equipment Financing• Commercial Real Estate (Purchase, Fix & Flip, Rehab, Renovations)• Business Acquisitions• Business ExpansionWe like the websites:www.quillmorecf.com they are in the same industry and provide the same servicesWe are wanting to be able to update when we do press releases and such using Word Press. Our look should be very professional and we will be adding Our Team Professional Bios and Headshots.

Industry/Entity Type

Finance

Number of Pages Required

5+ page

Font styles to use
Serif
Sans Serif

Requirements
Must have
• We want to copy quillmorecf.com
• We need:
• Home Page
• About Us
• Loan Programs
• Loan Criteria
• News
• Apply Now
• Contact
Nice to have
• See quillmorecf.com
Should not have
• Need professional design. Nothing bright or abstract

```html
<!DOCTYPE html>
<html lang="en">
<head>
<meta charset="utf-8">
<title>Corvane Lending Partners</title>
<link href="https://fonts.googleapis.com/css2?family=Open+Sans:wght@400;600;700&display=swap" rel="stylesheet">
<style>
:root{
  --blue:#1f5ca8;
  --navy:#0f2a4f;
  --ink:#222;
  --muted:#555;
  --grey-band:#e6e6e6;
  --card:#f1f1f1;
  --white:#fff;
}
*{margin:0;padding:0;box-sizing:border-box}
html,body{width:1200px;height:3797px;overflow:hidden;background:var(--white)}
body{font-family:"Open Sans",Arial,sans-serif;color:var(--ink)}
.page{position:relative;width:1200px;height:3797px;overflow:hidden}
.abs{position:absolute}

/* header */
.brand{left:144px;top:44px;font-size:24px;font-weight:700;color:var(--blue);display:flex;align-items:center;gap:10px;white-space:nowrap}
.brand .mark{width:16px;height:16px;background:var(--blue)}
.contact-bar{right:144px;top:20px;font-size:16px;font-weight:600;display:flex;gap:24px}
.contact-bar span{display:flex;align-items:center;gap:7px}
.main-nav{right:144px;top:77px;display:flex;gap:30px;font-size:14px}
.main-nav .active{color:var(--blue)}

/* hero */
.hero{left:0;top:121px;width:1200px;height:569px;clip-path:polygon(0 0,100% 0,100% 86%,0 100%);
  background:
    radial-gradient(ellipse 260px 300px at 330px 210px,rgba(214,186,160,.85),transparent 70%),
    radial-gradient(ellipse 360px 260px at 260px 470px,rgba(150,180,214,.9),transparent 70%),
    radial-gradient(ellipse 300px 220px at 560px 480px,rgba(196,150,120,.8),transparent 70%),
    linear-gradient(100deg,#4a4f57 0%,#6f6a63 30%,#8d7e6c 55%,#5a4c40 78%,#2f2a26 100%)}
.hero-title{right:144px;top:300px;text-align:right;color:var(--white);font-size:33px;font-weight:700;line-height:40px;letter-spacing:.3px;text-shadow:0 1px 3px rgba(0,0,0,.35)}
.hero-btn{left:871px;top:385px;width:182px;height:44px;background:var(--blue);color:var(--white);font-size:15px;font-weight:600;display:flex;align-items:center;justify-content:center}
.hero-arrow{top:352px}
.stats-band{left:0;top:608px;width:1200px;height:296px;background:var(--grey-band);clip-path:polygon(0 28%,100% 0,100% 76%,0 100%)}
.stat{top:724px;width:220px}
.stat h4{font-size:12px;font-weight:400}
.stat .amount{font-size:27px;font-weight:600;color:var(--blue);line-height:33px}
.stat p{font-size:9.5px;line-height:12px}

/* welcome */
.section-title{left:0;width:1200px;text-align:center;font-size:32px;font-weight:600;color:var(--blue)}
.welcome-text{left:144px;top:1022px;width:912px;text-align:center;font-size:13px;line-height:23px;color:var(--muted)}

/* feature band */
.feature-photo{left:0;top:1170px;width:1200px;height:480px;clip-path:polygon(0 7%,100% 0,100% 87%,0 100%);
  background:
    radial-gradient(ellipse 300px 180px at 420px 220px,rgba(235,230,222,.9),transparent 70%),
    radial-gradient(ellipse 220px 160px at 780px 250px,rgba(230,170,90,.55),transparent 70%),
    radial-gradient(ellipse 260px 200px at 1000px 300px,rgba(190,140,110,.8),transparent 70%),
    linear-gradient(120deg,#2a3242 0%,#3e4656 30%,#8b8c8e 55%,#5c5248 78%,#2a2a2c 100%)}
.info-box{background:var(--blue);color:var(--white);padding:20px 17px}
.info-box p{font-size:12.5px;line-height:19px;margin-bottom:9px}
.info-box ul{list-style:none;font-size:12.5px;font-weight:600;line-height:25px}
.info-box li::before{content:"•";margin-right:9px}

/* services */
.service{width:291px}
.service .photo{height:206px}
.service h3{margin-top:16px;text-align:center;font-size:18px;font-weight:600}

/* funding band */
.funding-photo{left:0;top:2772px;width:1200px;height:476px;clip-path:polygon(0 14%,100% 0,100% 94%,0 100%);
  background:
    radial-gradient(ellipse 140px 90px at 420px 230px,rgba(150,150,150,.75),transparent 70%),
    radial-gradient(ellipse 130px 80px at 800px 200px,rgba(140,140,140,.7),transparent 70%),
    radial-gradient(ellipse 110px 70px at 100px 380px,rgba(120,120,120,.6),transparent 70%),
    radial-gradient(ellipse 420px 240px at 620px 390px,rgba(70,72,78,.9),transparent 75%),
    linear-gradient(180deg,#17181b 0%,#26282c 50%,#0f1012 100%)}

/* team */
.team-card{top:3380px;width:294px;height:134px;background:var(--card);display:flex;padding:10px}
.team-card .head{width:112px;height:114px;flex:none}
.team-card .bio{padding-left:12px}
.team-card h4{font-size:16px;font-weight:600;margin-top:4px}
.team-card .role{font-size:10px;margin-bottom:6px}
.team-card p{font-size:8px;line-height:11px;color:var(--muted)}
.team-card .more{font-size:8px;font-weight:700;margin-top:3px}

/* footer */
.footer{left:0;top:3592px;width:1200px;height:205px;background:var(--navy);clip-path:polygon(0 26%,100% 0,100% 100%,0 100%)}
.footer-nav{left:144px;top:3706px;font-size:12px;color:var(--white);display:flex;gap:9px}
.copyright{left:144px;top:3740px;font-size:12px;color:var(--white)}
.social{top:3724px;width:18px;height:18px;border-radius:50%;border:2px solid var(--white)}
</style>
</head>
<body>
<div class="page">

  <header>
    <div class="abs brand"><span class="mark"></span>Corvane Lending Partners</div>
    <div class="abs contact-bar">
      <span><svg width="14" height="14" viewBox="0 0 24 24"><path fill="#222" d="M6.6 10.8a15 15 0 0 0 6.6 6.6l2.2-2.2c.3-.3.7-.4 1-.2 1.1.4 2.3.6 3.6.6.6 0 1 .4 1 1V20c0 .6-.4 1-1 1A17 17 0 0 1 3 4c0-.6.4-1 1-1h3.5c.6 0 1 .4 1 1 0 1.3.2 2.5.6 3.6.1.3 0 .7-.2 1z"/></svg>555 208 4417</span>
      <span><svg width="15" height="12" viewBox="0 0 24 18"><rect width="24" height="18" rx="2" fill="#222"/><path d="M1 2l11 8 11-8" stroke="#fff" stroke-width="2" fill="none"/></svg>info@corvanelending.com</span>
    </div>
    <nav class="abs main-nav">
      <span class="active">Home</span><span>About Us</span><span>Loan Programs</span><span>Loan Criteria</span><span>News</span><span>Apply Now</span><span>Contact</span>
    </nav>
  </header>

  <section>
    <div class="abs hero" role="img" aria-label="Smiling businessman in glasses shaking hands in an office"></div>
    <div class="abs hero-title">NAM TEMPUS QUAM<br>BIBENDUM VULPUTATE</div>
    <div class="abs hero-btn">GET STARTED NOW</div>
    <svg class="abs hero-arrow" style="left:52px" width="22" height="32" viewBox="0 0 24 34"><path d="M20 3L5 17l15 14" stroke="#fff" stroke-width="4" fill="none"/></svg>
    <svg class="abs hero-arrow" style="left:1126px" width="22" height="32" viewBox="0 0 24 34"><path d="M4 3l15 14L4 31" stroke="#fff" stroke-width="4" fill="none"/></svg>

    <div class="abs stats-band"></div>
    <div class="abs stat" style="left:144px"><h4>Maecenas vel tortor</h4><div class="amount">$3,245,000</div><p>Pellentesque convallis molestie enim sit amet efficitur.</p></div>
    <div class="abs stat" style="left:382px"><h4>Vivamus lacus</h4><div class="amount">$2,850,000</div><p>Pellentesque convallis molestie enim sit amet efficitur.</p></div>
    <div class="abs stat" style="left:618px"><h4>Cras augue magna</h4><div class="amount">$2,355,000</div><p>Pellentesque convallis molestie enim sit amet efficitur.</p></div>
    <div class="abs stat" style="left:856px"><h4>Aenean placerat</h4><div class="amount">$3,655,000</div><p>Pellentesque convallis molestie enim sit amet efficitur.</p></div>
  </section>

  <section>
    <h2 class="abs section-title" style="top:973px">Welcome to Corvane</h2>
    <p class="abs welcome-text">Vestibulum condimentum, risus ut posuere cursus, velit justo accumsan sem, lobortis aliquet metus dui libero. Pellentesque a imperdiet dolor, et auctor est. Fusce sollicitudin lorem et luctus volutpat. Proin placerat dapibus gravida. In tristique tristique nulla eget hendrerit. Maecenas vel tortor accumsan quam varius imperdiet vel eget elit. Aenean facilisis tincidunt lectus, id dictum nisi luctus eget.</p>
  </section>

  <section>
    <div class="abs feature-photo" role="img" aria-label="Hands holding a smartphone showing financial charts over a desk"></div>
    <div class="abs info-box" style="left:144px;top:1170px;width:327px;height:212px">
      <p>Many of our programs offer flexible guidelines to overcome common obstacles such as...</p>
      <ul><li>Credit Score</li><li>Credit History</li><li>Time in business</li><li>Financials</li><li>Industry type</li></ul>
    </div>
  </section>

  <section>
    <h2 class="abs section-title" style="top:1721px">We provide these services</h2>
    <div class="abs service" style="left:144px;top:1795px"><div class="photo" role="img" aria-label="Business team reviewing charts at a desk" style="background:radial-gradient(ellipse at 70% 40%,#f3ede4,transparent 60%),linear-gradient(135deg,#5a4634,#a58a6c 50%,#e6dccd)"></div><h3>Working Capital</h3></div>
    <div class="abs service" style="left:456px;top:1795px"><div class="photo" role="img" aria-label="Hands with calculator and documents" style="background:radial-gradient(ellipse at 40% 40%,#e8e4df,transparent 60%),linear-gradient(135deg,#7a6e62,#b9b0a6 55%,#4c4540)"></div><h3>Debt Consolidations</h3></div>
    <div class="abs service" style="left:765px;top:1795px"><div class="photo" role="img" aria-label="Payroll binder with calculator and forms" style="background:linear-gradient(170deg,#3d86c8 0%,#6aa8dc 40%,#e9e9e9 60%,#d5d5d5 100%)"></div><h3>Payroll</h3></div>

    <div class="abs service" style="left:144px;top:2084px"><div class="photo" role="img" aria-label="Hands with scissors, laptop and office supplies" style="background:radial-gradient(ellipse at 50% 65%,#f4f2ef,transparent 60%),linear-gradient(135deg,#d98e3f,#e6c9a4 45%,#ece8e3)"></div><h3>Operating Expenses</h3></div>
    <div class="abs service" style="left:456px;top:2084px"><div class="photo" role="img" aria-label="Warehouse aisle stacked with boxed inventory" style="background:radial-gradient(ellipse at 50% 45%,#e2e6ea,transparent 45%),linear-gradient(180deg,#6e7b89,#a3acb6 60%,#c9ccd0)"></div><h3>Inventory</h3></div>
    <div class="abs service" style="left:765px;top:2084px"><div class="photo" role="img" aria-label="Rows of industrial air conditioning units" style="background:linear-gradient(160deg,#c5cbd1 0%,#8d96a0 40%,#3a4047 100%)"></div><h3>Equipment Financing</h3></div>

    <div class="abs service" style="left:144px;top:2372px"><div class="photo" role="img" aria-label="Businessman holding a model office building" style="background:radial-gradient(ellipse at 50% 70%,#5f8fb5,transparent 35%),linear-gradient(90deg,#c9ccd1,#2b2f36 40%,#2b2f36 60%,#c0c4c9)"></div><h3>Commercial Real Estate</h3></div>
    <div class="abs service" style="left:456px;top:2372px"><div class="photo" role="img" aria-label="Businessman holding two puzzle pieces" style="background:radial-gradient(ellipse at 50% 60%,#d9d7d2,transparent 35%),linear-gradient(135deg,#7a643f,#3a3a3c 50%,#1b212b)"></div><h3>Business Acquisitions</h3></div>
    <div class="abs service" style="left:765px;top:2372px"><div class="photo" role="img" aria-label="Green board with rising arrow and notes" style="background:radial-gradient(ellipse at 55% 35%,#3fb06b,transparent 55%),linear-gradient(135deg,#9bd0a0,#2f8a55 45%,#a9865a)"></div><h3>Business Expansion</h3></div>
  </section>

  <section>
    <div class="abs funding-photo" role="img" aria-label="Stacks of coins on a dark surface with a compass"></div>
    <div class="abs info-box" style="left:729px;top:2699px;width:324px;height:172px">
      <p>Our streamlined funding process makes</p>
      <ul><li>Getting a business loan</li><li>Business line of credit</li><li>Stated income commercial real estate loan</li><li>A smooth and stress free experience</li></ul>
    </div>
  </section>

  <section>
    <h2 class="abs section-title" style="top:3322px">Our Team</h2>
    <svg class="abs" style="left:56px;top:3436px" width="14" height="24" viewBox="0 0 14 24"><path d="M12 2L2 12l10 10" stroke="#999" stroke-width="2" fill="none"/></svg>
    <svg class="abs" style="left:1130px;top:3436px" width="14" height="24" viewBox="0 0 14 24"><path d="M2 2l10 10L2 22" stroke="#999" stroke-width="2" fill="none"/></svg>

    <div class="abs team-card" style="left:144px"><div class="head" role="img" aria-label="Headshot of team member William" style="background:radial-gradient(ellipse at 50% 45%,#b59a84,transparent 55%),linear-gradient(135deg,#7d7d7d,#d6d6d6)"></div><div class="bio"><h4>William</h4><div class="role">Proin ut enim</div><p>Senior lending advisor helping owners secure capital for growth and daily operations.</p><div class="more">More</div></div></div>
    <div class="abs team-card" style="left:456px"><div class="head" role="img" aria-label="Headshot of team member Sophia" style="background:radial-gradient(ellipse at 50% 45%,#e9c9a8,transparent 55%),linear-gradient(135deg,#c99a5e,#efe5d8)"></div><div class="bio"><h4>Sophia</h4><div class="role">Donec aliquam quam</div><p>Funding specialist guiding clients through credit lines and commercial property loans.</p><div class="more">More</div></div></div>
    <div class="abs team-card" style="left:765px"><div class="head" role="img" aria-label="Headshot of team member Alexander" style="background:radial-gradient(ellipse at 50% 45%,#b48a6c,transparent 55%),linear-gradient(135deg,#4e4038,#a8947f)"></div><div class="bio"><h4>Alexander</h4><div class="role">Nullam aliquam quam</div><p>Client relations lead making each application smooth, clear and stress free.</p><div class="more">More</div></div></div>
  </section>

  <footer>
    <div class="abs footer"></div>
    <nav class="abs footer-nav"><span>Home</span>|<span>About Us</span>|<span>Loan Programs</span>|<span>Loan Criteria</span>|<span>News</span>|<span>Apply Now</span>|<span>Contact</span></nav>
    <div class="abs copyright">Copyright © 2018 Corvane. All rights reserved.</div>
    <div class="abs social" style="left:1000px"></div>
    <div class="abs social" style="left:1036px"></div>
  </footer>

</div>
</body>
</html>
```